Meridale Nutrition needs Stationary and a business card

We would like to use our current logo. The text can be moved around as needed. The stationary needs to be a 'first page' where the logo is more prominent to be impressive on higher quality paper and a second page where the logo is more subtle where there will be much more information on the page. There are 2 clinic locations which will need include name, address, phone number, fax number, web address. The business card should be single sided and contain this information also.
The design must be contemporary and sophisticated as this is a science based diet run out of a medical clinic.

Target Market(s)

People wanting to lose weight, athletes looking to optimise performance, people with arthritis or fighting cancer

Industry/Entity Type

Business

Contact Information for Business Card

must use the logo. I have attached an example card with the practice details on it. there must be space for the doctors name. Also the website www.meridalenutrition.com.au

Requirements
Must have
• the logo, the business adresses and phone numbers, the website, the doctors name and qualifications
Nice to have
• some creativity
Should not have
• Do not simply reproduce the existing card please

```html
<!DOCTYPE html>
<html lang="en">
<head>
<meta charset="utf-8">
<title>Meridale Nutrition Stationery</title>
<link href="https://fonts.googleapis.com/css2?family=Nunito+Sans:wght@300;400;800&display=swap" rel="stylesheet">
<style>
  :root {
    --stage: #d1d2d4;
    --navy: #34679a;
    --sky: #35c4f0;
    --paper: #ffffff;
    --grey-text: #8a8f96;
    --faint: #eef1f6;
  }
  html, body { margin: 0; padding: 0; overflow: hidden; }
  body {
    width: 1200px;
    height: 926px;
    background: var(--stage);
    font-family: "Nunito Sans", Arial, sans-serif;
    position: relative;
  }
  .sheet {
    position: absolute;
    top: 110px;
    width: 546px;
    height: 705px;
    overflow: hidden;
    box-shadow: 6px 6px 10px rgba(0,0,0,0.35);
  }
  .letterhead { left: 31px; background: var(--paper); }
  .cover { left: 622px; background: var(--navy); }

  .letterhead .seal {
    position: absolute;
    left: 22px;
    top: 18px;
    width: 60px;
    height: 60px;
    border-radius: 50%;
    background: var(--sky);
    border: 2px solid var(--navy);
    box-sizing: border-box;
  }
  .letterhead .wordmark {
    position: absolute;
    right: 28px;
    top: 27px;
    margin: 0;
    text-align: center;
    color: var(--navy);
    font-weight: 800;
    line-height: 1;
  }
  .letterhead .wordmark .main { display: block; font-size: 27px; letter-spacing: -0.3px; }
  .letterhead .wordmark .sub { display: block; font-size: 13px; letter-spacing: 5px; margin-top: 2px; }
  .letterhead .watermark {
    position: absolute;
    left: 345px;
    top: 507px;
    width: 173px;
    height: 173px;
    border-radius: 50%;
    background: var(--faint);
  }
  .locations {
    position: absolute;
    left: 309px;
    top: 604px;
    display: flex;
    font-size: 11px;
    font-weight: 300;
    line-height: 12.8px;
    color: var(--grey-text);
  }
  .location { padding-right: 8px; }
  .location + .location { border-left: 1.5px solid var(--navy); padding-left: 8px; }
  .location h3 {
    margin: 0;
    font-size: 12.5px;
    font-weight: 800;
    color: var(--navy);
    line-height: 13px;
  }
  .location p { margin: 0; }
  .location b { color: var(--navy); font-weight: 800; }
  .wave { position: absolute; left: 0; bottom: 0; display: block; }
  .specialties {
    position: absolute;
    left: 35px;
    top: 670px;
    display: flex;
    color: #fff;
    font-size: 11px;
    font-weight: 300;
    line-height: 13px;
  }
  .specialty { padding-right: 7px; }
  .specialty + .specialty { border-left: 1px solid #fff; padding-left: 7px; }
  .specialty p { margin: 0; }

  .cover .emblem {
    position: absolute;
    left: 159px;
    top: 178px;
    width: 228px;
    height: 228px;
    border-radius: 50%;
    background: var(--sky);
    border: 5px solid #fff;
    box-sizing: border-box;
  }
  .cover .title {
    position: absolute;
    left: 0;
    width: 546px;
    top: 545px;
    margin: 0;
    text-align: center;
    color: #fff;
    font-weight: 800;
    line-height: 1;
  }
  .cover .title .main { display: block; font-size: 50px; letter-spacing: -0.5px; }
  .cover .title .sub { display: block; font-size: 28px; letter-spacing: 10px; margin-top: 4px; }
</style>
</head>
<body>
  <section class="sheet letterhead">
    <div class="seal"></div>
    <h1 class="wordmark"><span class="main">MERIDALE</span><span class="sub">NUTRITION</span></h1>
    <div class="watermark"></div>
    <div class="locations">
      <div class="location">
        <h3>Ashvale</h3>
        <p>47-49 Linden Road</p>
        <p>Ashvale NSW 2190</p>
        <p><b>T:</b> 02 9000 1234</p>
      </div>
      <div class="location">
        <h3>Kellbrook</h3>
        <p>160 Harbour Road</p>
        <p>Kellbrook NSW 2095</p>
        <p><b>F:</b> 02 9000 5678</p>
      </div>
    </div>
    <svg class="wave" width="546" height="67" viewBox="0 0 546 67">
      <path d="M0 26 C 80 0, 180 2, 300 22 S 480 46, 546 36 L546 67 L0 67 Z" fill="var(--sky)"/>
      <path d="M0 33 C 80 10, 180 12, 300 30 S 480 52, 546 40 L546 67 L0 67 Z" fill="#fff"/>
      <path d="M0 36 C 80 14, 180 16, 300 34 S 480 56, 546 44 L546 67 L0 67 Z" fill="var(--navy)"/>
    </svg>
    <div class="specialties">
      <div class="specialty"><p>Shoulder and Elbow</p><p>www.meridalenutrition.com.au</p></div>
      <div class="specialty"><p>Knee Surgery</p><p>info@meridalenutrition.com.au</p></div>
    </div>
  </section>

  <section class="sheet cover">
    <div class="emblem"></div>
    <h2 class="title"><span class="main">MERIDALE</span><span class="sub">NUTRITION</span></h2>
    <svg class="wave" width="546" height="70" viewBox="0 0 546 70">
      <path d="M0 24 C 120 50, 240 40, 360 24 S 510 0, 546 20 L546 70 L0 70 Z" fill="#fff"/>
      <path d="M0 28 C 120 54, 240 44, 360 28 S 510 4, 546 24 L546 70 L0 70 Z" fill="var(--navy)"/>
      <path d="M0 32 C 120 58, 240 48, 360 32 S 510 8, 546 28 L546 70 L0 70 Z" fill="var(--sky)"/>
    </svg>
  </section>
</body>
</html>
```